wordpress website Carla Winfield, Author, Speaker and Coach

Need a wordpress blogging website for author/speaker/coach.
I have paid for hosting on nestparrot.
I am currently writing a book - Launchpad to Campus - Steps and strategies to prepare you to thrive in college and beyond. Eventually, I will have an Academic/Life Coaching program targeting high school and college students. This website's purpose is to build my email list. I can offer the following reports as incentive for email sign-up:
1. Six Habits That Get Your Teen Through University On Schedule and Debt-Light
2. Surprising Routes to Fund Your Degree
3. Entrance exam vocabulary word of the day

facebook page: https://www.facebook.com/Carla-Winfield-AcademicLife-Coach-918273645501928/

I would like to have these pages:

1. Home or About page

High school is becoming more and more stressful for students. Not only are they taking more honors classes than ever before, and often spending $1,000’s on entrance-exam prep programs, most are NOT prepared for success in college. Only 19% of students are graduating from college within 4 years and only 56% are graduating within 6 years. With the cost of higher education skyrocketing, each extra year of school can costs families $40,000 - $60,000 when you factor in living expenses. Then, when students do graduate, they are often underemployed.

Carla's approach is whole person oriented. Her programs help students learn life skills in addition to the study, time management skills, etc. offered by most academic coaching programs. Our program addresses all of the major causes of failure to graduate within 4 years, and is based on sound educational research. Carla's program initially provides the daily interaction needed to successfully change behaviors and seat new success habits, unlike many programs in which students interact with coaches only once a week.
Bio
Carla Winfield is a certified teacher and holds advanced certification in academic coaching and tutoring. She also is a certified trainer in the Morris Tellwright Achievement Keys. She has three successful adult children, and helped them overcome learning differences and thrive.

2. Blog

3. Contact - Include form (I split time between USA and Saudi Arabia, so I will call or email people back, but don't want to leave a phone number)
info@carlawinfield.example

4. Store – 1 book for now
Launchpad to Campus
Steps and strategies to prepare you to thrive in college and beyond
Available 12/01/2017
I could make a preview chapter available for download

5. Speaking
Carla Winfield is available for keynote addresses and half-day, full day or multi-day workshops. I will develop details later

6.Coaching programs
I will develop details later

Target Market(s)

high school students who are college bound and their parents

Number of Pages Required

5+ page

Font styles to use
Sans Serif

Colors

Designer to choose colors to be used in the design.

Requirements
Nice to have
• integration with post finch for contact management

```html
<!DOCTYPE html>
<html lang="en">
<head>
<meta charset="utf-8">
<title>Carla Winfield — Author, Speaker and Coach</title>
<link rel="stylesheet" href="https://fonts.googleapis.com/css2?family=Roboto+Condensed:wght@400;700&family=Open+Sans:wght@400;600&family=Roboto:wght@400;500&display=swap">
<style>
:root{
  --green:#1f8a4c;
  --green-dark:#17723d;
  --lime:#8cc63f;
  --purple:#8a87c4;
  --ink:#2b2b2b;
  --text:#555;
  --muted:#777;
  --pale-blue:#f1f7fb;
  --pale-grey:#efefef;
  --footer:#f5f5f5;
  --white:#fff;
  --dark:#2a2a2a;
}
*{box-sizing:border-box;margin:0;padding:0}
html,body{width:1200px;height:3025px;overflow:hidden}
body{position:relative;background:var(--white);font-family:"Open Sans",Arial,sans-serif;color:var(--text)}
.abs{position:absolute}
.cond{font-family:"Roboto Condensed","Arial Narrow",sans-serif}

/* header */
.site-header{position:absolute;left:0;top:0;width:1200px;height:112px;background:var(--white);z-index:3}
.logo-bulge{position:absolute;left:70px;top:-40px;width:190px;height:190px;border-radius:50%;background:var(--white);z-index:3}
.brand{position:absolute;left:100px;top:22px;display:flex;align-items:center;gap:12px;z-index:4}
.brand-dot{width:30px;height:30px;border-radius:50%;background:var(--green)}
.brand-name{font-family:"Roboto Condensed",sans-serif;font-size:40px;font-weight:700;color:var(--green)}
.top-contact{position:absolute;right:100px;top:20px;display:flex;gap:34px;font-family:"Roboto",sans-serif;font-size:14px;color:var(--ink);z-index:4}
.top-contact span{display:flex;align-items:center;gap:10px}
.ico-round{width:26px;height:26px;border-radius:50%;background:var(--green);display:flex;align-items:center;justify-content:center}
.main-nav{position:absolute;right:100px;top:72px;display:flex;gap:28px;font-family:"Roboto",sans-serif;font-size:13px;color:var(--ink);z-index:4}
.main-nav a{color:inherit;text-decoration:none;padding-bottom:14px}
.main-nav a.current{color:var(--green);font-weight:500;border-bottom:3px solid var(--green)}

/* hero */
.hero{position:absolute;left:0;top:112px;width:1200px;height:560px}
.hero-photo{position:absolute;inset:0;background:linear-gradient(100deg,#3b3b3b 0%,#565350 45%,#4a4440 70%,#6b5a4c 100%)}
.hero-title{position:absolute;left:140px;top:205px;font-size:42px;color:var(--white);letter-spacing:.5px}
.hero-sub{position:absolute;left:140px;top:262px;width:400px;font-size:14px;line-height:28px;color:var(--white);font-weight:700}
.btn-green{position:absolute;left:142px;top:333px;width:126px;height:36px;border-radius:18px;background:var(--green);color:var(--white);font:700 13px "Roboto Condensed",sans-serif;display:flex;align-items:center;justify-content:center}
.book{position:absolute;left:708px;top:106px;width:288px;height:364px;background:linear-gradient(180deg,#7c8a9c 0%,#8a8f85 45%,#4f8a45 62%,#1f8a4c 64%,#1f8a4c 100%);box-shadow:6px 6px 14px rgba(0,0,0,.4)}
.book-title{position:absolute;left:0;right:0;top:270px;text-align:center;color:var(--white);font-size:24px;font-weight:700}
.book-sub{position:absolute;left:30px;right:30px;top:305px;text-align:center;color:var(--white);font-size:12px;line-height:18px}
.hero-arrow{position:absolute;top:232px}

/* welcome */
.welcome{position:absolute;left:0;top:672px;width:1200px;height:510px;background:var(--pale-blue)}
.portrait{position:absolute;left:132px;top:88px;width:344px;height:344px;border-radius:50%;border:5px solid var(--purple);background:var(--white);padding:6px}
.portrait div{width:100%;height:100%;border-radius:50%;background:radial-gradient(circle at 50% 40%,#b98f76 0%,#6b4a3c 50%,#3a2a26 100%)}
h2.section-title{font-family:"Roboto Condensed",sans-serif;font-weight:400;color:var(--ink);font-size:32px}
.welcome h2{position:absolute;left:510px;top:118px}
.welcome p{position:absolute;left:510px;width:560px;font-size:11px;line-height:22px;color:var(--text)}
.btn-purple{position:absolute;left:510px;top:376px;width:104px;height:30px;border-radius:15px;background:var(--purple);color:var(--white);font-size:10px;font-weight:600;display:flex;align-items:center;justify-content:center;gap:4px}

/* services */
.services{position:absolute;left:0;top:1182px;width:1200px;height:608px;background:var(--white)}
.services h2{position:absolute;left:0;width:1200px;top:85px;text-align:center}
.services .intro{position:absolute;left:0;width:1200px;top:130px;text-align:center;font-size:11px;line-height:21px;color:var(--muted)}
.service-card{position:absolute;top:240px;width:314px;height:260px;color:var(--white);text-align:center;box-shadow:0 10px 12px -6px rgba(0,0,0,.25)}
.service-card.lime{background:var(--lime)}
.service-card.purple{background:var(--purple)}
.service-card .tab{position:absolute;left:97px;top:-60px;width:120px;height:120px;border-radius:50%;background:var(--white);display:flex;align-items:flex-end;justify-content:center;padding-bottom:22px}
.service-card h3{position:absolute;left:0;right:0;top:86px;font:400 18px "Roboto Condensed",sans-serif}
.service-card p{position:absolute;left:34px;right:34px;top:118px;font-size:11px;line-height:21px}
.service-card .more{position:absolute;left:0;right:0;top:218px;font:700 14px "Roboto Condensed",sans-serif;letter-spacing:1px}

/* blog */
.blog{position:absolute;left:0;top:1790px;width:1200px;height:540px;background:var(--pale-grey)}
.blog h2{position:absolute;left:0;width:1200px;top:70px;text-align:center}
.post{position:absolute;top:153px;width:480px;height:247px;background:var(--white);box-shadow:0 2px 6px rgba(0,0,0,.12)}
.post .thumb{position:absolute;left:0;top:0;width:216px;height:247px}
.post .body{position:absolute;left:240px;top:18px;width:220px}
.post h4{font:400 15px/19px "Roboto",sans-serif;color:var(--ink)}
.post .date{margin-top:14px;font:italic 12px "Roboto",sans-serif;color:var(--green)}
.post p{margin-top:10px;font-size:10px;line-height:17px;color:var(--muted)}
.post .read{margin-top:10px;font:400 12px "Roboto",sans-serif;color:var(--ink)}

/* newsletter */
.newsletter{position:absolute;left:0;top:2300px;width:1200px;height:380px}
.newsletter h2{position:absolute;left:113px;top:117px;font:700 28px "Roboto Condensed",sans-serif;color:var(--white)}
.offers{position:absolute;left:113px;top:170px;list-style:none;color:var(--white);font:700 13.5px "Roboto Condensed",sans-serif}
.offers li{display:flex;align-items:center;gap:9px;height:28px}
.field{position:absolute;left:687px;width:388px;height:40px;background:var(--white);font-size:11px;color:var(--muted);display:flex;align-items:center;justify-content:center}
.subscribe{position:absolute;left:687px;top:230px;width:388px;height:40px;background:var(--dark);color:var(--white);font:700 16px "Roboto Condensed",sans-serif;display:flex;align-items:center;justify-content:center}

/* footer */
.site-footer{position:absolute;left:0;top:2680px;width:1200px;height:290px;background:var(--footer)}
.col-rule{position:absolute;top:0;width:1px;height:290px;background:#e1e1e1}
.badge{position:absolute;left:102px;top:42px;width:176px;height:176px;border-radius:50%;background:radial-gradient(circle at 40% 35%,#e6e6e6,#a9a9a9)}
.site-footer h5{position:absolute;font:400 18px "Roboto Condensed",sans-serif;color:var(--ink)}
.contact-list{position:absolute;left:405px;top:90px;list-style:none;font-size:12px;color:var(--text)}
.contact-list li{display:flex;gap:12px;margin-bottom:16px;line-height:19px}
.quick{position:absolute;left:752px;top:90px;list-style:none;font-size:11px;color:var(--text)}
.quick li{height:20.5px;display:flex;align-items:center;gap:10px}
.social{position:absolute;left:998px;top:86px;list-style:none;font-size:13px;color:var(--text)}
.social li{display:flex;align-items:center;gap:9px;height:34px}
.social .ring{width:26px;height:26px;border:1px solid #8a8a8a;border-radius:50%}
.copyright{position:absolute;left:0;top:2970px;width:1200px;height:55px;border-top:1px solid #ddd;background:var(--white);font-size:11px;color:var(--muted);display:flex;align-items:center;justify-content:center}
</style>
</head>
<body>

<header class="site-header">
  <div class="logo-bulge"></div>
  <div class="brand"><span class="brand-dot"></span><span class="brand-name">Carla Winfield</span></div>
  <div class="top-contact">
    <span><i class="ico-round"><svg width="13" height="13" viewBox="0 0 24 24"><path fill="#fff" d="M6.6 10.8a15 15 0 0 0 6.6 6.6l2.2-2.2c.3-.3.7-.4 1-.2 1.1.4 2.3.6 3.6.6.6 0 1 .4 1 1V20c0 .6-.4 1-1 1A17 17 0 0 1 3 4c0-.6.4-1 1-1h3.5c.6 0 1 .4 1 1 0 1.3.2 2.5.6 3.6.1.3 0 .7-.2 1z"/></svg></i>+99(0) 5172 8830</span>
    <span><i class="ico-round"><svg width="13" height="13" viewBox="0 0 24 24"><path fill="#fff" d="M3 5h18v14H3zm2 2v.5l7 4.5 7-4.5V7z"/></svg></i>info@carlawinfield.example</span>
  </div>
  <nav class="main-nav">
    <a class="current">HOME</a><a>BLOG</a><a>STORE</a><a>SPEAKING</a><a>COACHING PROGRAM</a><a>CONTACT</a>
  </nav>
</header>

<section class="hero">
  <div class="hero-photo" role="img" aria-label="Dim photo of a sandy beach with a woman in a sun hat on the right"></div>
  <svg class="abs" style="left:0;top:500px" width="1200" height="60" viewBox="0 0 1200 60"><path d="M0 42 Q600 -28 1200 42 L1200 60 L0 60Z" fill="#f1f7fb"/><path d="M0 42 Q600 -28 1200 42" fill="none" stroke="#8a87c4" stroke-width="4"/></svg>
  <svg class="hero-arrow" style="left:42px" width="34" height="64" viewBox="0 0 34 64"><path d="M32 2 2 32l30 30" fill="none" stroke="#fff" stroke-width="2"/></svg>
  <svg class="hero-arrow" style="left:1126px" width="34" height="64" viewBox="0 0 34 64"><path d="M2 2l30 30L2 62" fill="none" stroke="#fff" stroke-width="2"/></svg>
  <h1 class="hero-title cond" style="font-weight:400">LAUNCHPAD TO CAMPUS</h1>
  <p class="hero-sub cond">STEPS AND STRATEGIES TO PREPARE YOU TO THRIVE IN COLLEGE AND BEYOND</p>
  <a class="btn-green">READ MORE</a>
  <div class="book" role="img" aria-label="Book cover with a campus building and a student on the lawn">
    <div class="book-title cond">LAUNCHPAD TO CAMPUS</div>
    <div class="book-sub">Steps and strategies to prepare you to thrive in college and beyond</div>
  </div>
</section>

<section class="welcome">
  <div class="portrait"><div role="img" aria-label="Portrait photo of Carla Winfield"></div></div>
  <h2 class="section-title">WELCOME TO CARLA WINFIELD</h2>
  <p style="top:172px">High school is becoming more and more stressful for students. Not only are they taking more honors classes than ever before, and often spending $1,000’s on entrance-exam prep programs, most are NOT prepared for success in college. Only 19% of students are graduating from college within 4 years and only 56% are graduating within 6 years. With the cost of higher education skyrocketing, each extra year of school can costs families $40,000 - $60,000 when you factor in living expenses.</p>
  <p style="top:296px">Then, when students do graduate, they are often underemployed. Carla’s approach is whole person oriented. Her programs help students learn life skills in addition to the study, time management skills, etc. offered by most academic coaching programs. Our program addresses</p>
  <a class="btn-purple">READ MORE <svg width="10" height="10" viewBox="0 0 10 10"><circle cx="5" cy="5" r="5" fill="#fff"/><path d="M4 3l2 2-2 2" stroke="#8a87c4" fill="none" stroke-width="1.3"/></svg></a>
</section>

<section class="services">
  <h2 class="section-title">OUR SERVICES</h2>
  <p class="intro">Sed ut perspiciatis unde omnis iste natus error sit voluptatem<br>accusantium doloremque laudantium, totam rem aperiam, eaque ipsa quae ab illo inventore veritatis</p>

  <article class="service-card lime" style="left:100px">
    <div class="tab"><svg width="40" height="34" viewBox="0 0 40 34"><path d="M20 2 2 11l18 9 18-9z" fill="#1f8a4c"/><path d="M9 15v9c4 4 18 4 22 0v-9l-11 6z" fill="#1f8a4c"/><path d="M35 12v12" stroke="#1f8a4c" stroke-width="2"/></svg></div>
    <h3>ACADEMIC/LIFE</h3>
    <p>Lorem ipsum dolor sit amet, consectetur adipiscing elit. Aliquam viverra convallis auctor. Sed accumsan libero quis mi commodo et suscipit enim</p>
    <div class="more">[ MORE ]</div>
  </article>
  <article class="service-card purple" style="left:443px">
    <div class="tab"><svg width="42" height="34" viewBox="0 0 42 34"><path d="M4 12h8l20-9v26L12 20H4z" fill="#8a87c4"/><path d="M12 20l4 11h6l-3-10" fill="#8a87c4"/><path d="M36 10v10" stroke="#8a87c4" stroke-width="3"/></svg></div>
    <h3>SPEAKING</h3>
    <p>Lorem ipsum dolor sit amet, consectetur adipiscing elit. Aliquam viverra convallis auctor. Sed accumsan libero quis mi commodo et suscipit enim</p>
    <div class="more">[ MORE ]</div>
  </article>
  <article class="service-card lime" style="left:785px">
    <div class="tab"><svg width="36" height="40" viewBox="0 0 36 40"><rect x="4" y="2" width="26" height="34" fill="none" stroke="#1f8a4c" stroke-width="2.5"/><path d="M9 10h16M9 16h16M9 22h10" stroke="#1f8a4c" stroke-width="2"/><path d="M22 26l4 4 8-10" stroke="#1f8a4c" stroke-width="2.5" fill="none"/></svg></div>
    <h3>COACHING PROGRAM</h3>
    <p>Lorem ipsum dolor sit amet, consectetur adipiscing elit. Aliquam viverra convallis auctor. Sed accumsan libero quis mi commodo et suscipit enim</p>
    <div class="more">[ MORE ]</div>
  </article>
</section>

<section class="blog">
  <h2 class="section-title">LATEST BLOG</h2>
  <article class="post" style="left:100px">
    <div class="thumb" role="img" aria-label="Photo of two smiling students with a book" style="background:linear-gradient(135deg,#c9a27e,#7a5a46 60%,#4b3c35)"></div>
    <div class="body">
      <h4>Sed ut perspiciatis unde omnis natus error sit voluptatem</h4>
      <div class="date">SEP 19, 2017</div>
      <p>Sed ut perspiciatis unde omnis iste natus voluptatem accusantium doloremque laudantium, totam rem aperiam, eaque ipsa quae ab illo inventore veritatis et quasi architecto beatae vitae dicta</p>
      <div class="read">Read More +</div>
    </div>
  </article>
  <article class="post" style="left:618px">
    <div class="thumb" role="img" aria-label="Photo of a student reading with a laptop by a window" style="background:linear-gradient(135deg,#9aa57a,#5f6a48 55%,#3b3f33)"></div>
    <div class="body">
      <h4>Sed ut perspiciatis unde omnis natus error sit voluptatem</h4>
      <div class="date">SEP 19, 2017</div>
      <p>Sed ut perspiciatis unde omnis iste natus voluptatem accusantium doloremque laudantium, totam rem aperiam, eaque ipsa quae ab illo inventore veritatis et quasi architecto beatae vitae dicta</p>
      <div class="read">Read More +</div>
    </div>
  </article>
</section>

<section class="newsletter">
  <svg class="abs" style="left:0;top:0" width="1200" height="380" viewBox="0 0 1200 380" role="img" aria-label="Green-tinted photo of students in the background">
    <defs><linearGradient id="nlBg" x1="0" y1="0" x2="1" y2="1"><stop offset="0" stop-color="#1e8a4a"/><stop offset=".6" stop-color="#2a9a58"/><stop offset="1" stop-color="#1f8040"/></linearGradient></defs>
    <path d="M0 30 Q300 -10 600 25 T1200 10 V380 H0Z" fill="url(#nlBg)"/>
  </svg>
  <h2>SIGN UP FOR OUR NEWSLETTER</h2>
  <ul class="offers">
    <li><svg width="12" height="12" viewBox="0 0 12 12"><circle cx="6" cy="6" r="6" fill="#fff"/><path d="M5 3.5 7.5 6 5 8.5" stroke="#1f8a4c" stroke-width="1.5" fill="none"/></svg>Six Habits That Get Your Teen Through University On Schedule and Debt-Light</li>
    <li><svg width="12" height="12" viewBox="0 0 12 12"><circle cx="6" cy="6" r="6" fill="#fff"/><path d="M5 3.5 7.5 6 5 8.5" stroke="#1f8a4c" stroke-width="1.5" fill="none"/></svg>Surprising Routes to Fund Your Degree</li>
    <li><svg width="12" height="12" viewBox="0 0 12 12"><circle cx="6" cy="6" r="6" fill="#fff"/><path d="M5 3.5 7.5 6 5 8.5" stroke="#1f8a4c" stroke-width="1.5" fill="none"/></svg>Entrance exam vocabulary word of the day</li>
  </ul>
  <div class="field" style="top:125px">Enter Name</div>
  <div class="field" style="top:178px">Enter Email</div>
  <div class="subscribe">SUBSCRIBE</div>
</section>

<footer class="site-footer">
  <div class="col-rule" style="left:342px"></div>
  <div class="col-rule" style="left:693px"></div>
  <div class="col-rule" style="left:940px"></div>
  <div class="badge" role="img" aria-label="Certified trainer seal"></div>

  <h5 style="left:405px;top:50px">CONTACT US</h5>
  <ul class="contact-list">
    <li><svg width="12" height="16" viewBox="0 0 12 16"><path d="M6 0a6 6 0 0 0-6 6c0 4.5 6 10 6 10s6-5.5 6-10a6 6 0 0 0-6-6zm0 8.5A2.5 2.5 0 1 1 6 3.5a2.5 2.5 0 0 1 0 5z" fill="#666"/></svg><span>Carla Winfield<br>Lindenhof-Weg 12 40213 Eastbrook</span></li>
    <li><svg width="12" height="12" viewBox="0 0 24 24"><path fill="#666" d="M6.6 10.8a15 15 0 0 0 6.6 6.6l2.2-2.2c.3-.3.7-.4 1-.2 1.1.4 2.3.6 3.6.6.6 0 1 .4 1 1V20c0 .6-.4 1-1 1A17 17 0 0 1 3 4c0-.6.4-1 1-1h3.5c.6 0 1 .4 1 1 0 1.3.2 2.5.6 3.6.1.3 0 .7-.2 1z"/></svg><span>Phone: +44 710 55 21 908</span></li>
    <li><svg width="12" height="12" viewBox="0 0 24 24"><path fill="#666" d="M3 5h18v14H3zm2 2v.5l7 4.5 7-4.5V7z"/></svg><span>info@carlawinfield.example</span></li>
  </ul>

  <h5 style="left:752px;top:50px">QUICK LINKS</h5>
  <ul class="quick">
    <li>▸ Home</li><li>▸ About Us</li><li>▸ Coaching Program,</li><li>▸ Speaking</li><li>▸ Blog</li><li>▸ store</li><li>▸ Contact Us</li>
  </ul>

  <h5 style="left:998px;top:50px">SOCIAL</h5>
  <ul class="social">
    <li><span class="ring"></span>Friendbook</li>
    <li><span class="ring"></span>Chirper</li>
    <li><span class="ring"></span>Snapgram</li>
    <li><span class="ring"></span>Pinboard</li>
    <li><span class="ring"></span>Tubecast</li>
  </ul>
</footer>

<div class="copyright">©2017 Carla Winfield, All Rights Reserved.</div>

</body>
</html>
```